Business Card Design

I give lessons and clinics for dressage riders
I would like the design to be an outline (with broad lines) of a dressage horse and rider with in background of whole card with print over top tan or parchment card with burgundy print

Industry/Entity Type

Business

Contact Information for Business Card

Dale Ferrin
612-374-2059
Classical dressage training for the modern American
Clinics, lessons, training level -Prix St. George

Requirements
Must have
• broad lined outline of dressage horse and rider

```html
<!DOCTYPE html>
<html lang="en">
<head>
<meta charset="utf-8">
<title>Dale Ferrin — Classical Dressage Business Card</title>
<link rel="stylesheet" href="https://fonts.googleapis.com/css2?family=Alegreya+SC:wght@700;800&display=swap">
<style>
  :root {
    --parchment-center: #ecd3b6;
    --parchment-mid: #dfbf9f;
    --parchment-edge: #b98a72;
    --burgundy-ink: #560d27;
    --burgundy-tagline: #6a1230;
    --burgundy-frame: #4a0a20;
    --rose-art: #a04c58;
    --rose-art-light: #c07a7c;
  }
  * { margin: 0; padding: 0; box-sizing: border-box; }
  html, body {
    width: 1200px;
    height: 693px;
    overflow: hidden;
    background: var(--parchment-edge);
  }
  .business-card {
    position: relative;
    width: 1200px;
    height: 693px;
    overflow: hidden;
    background:
      radial-gradient(ellipse 70% 68% at 48% 48%, var(--parchment-center) 0%, var(--parchment-mid) 62%, var(--parchment-edge) 100%);
    font-family: "Alegreya SC", "Times New Roman", serif;
    color: var(--burgundy-ink);
  }
  .rider-illustration {
    position: absolute;
    left: 771px;
    top: 12px;
    width: 336px;
    height: 532px;
  }
  .card-frame {
    position: absolute;
    inset: 0;
    width: 1200px;
    height: 693px;
  }
  .contact-name,
  .contact-phone,
  .service-line {
    position: absolute;
    left: 92px;
    white-space: nowrap;
    text-transform: uppercase;
  }
  .contact-name {
    top: 420px;
    font-size: 58px;
    line-height: 64px;
    font-weight: 800;
    letter-spacing: 2px;
  }
  .contact-phone {
    top: 482px;
    font-size: 58px;
    line-height: 64px;
    font-weight: 800;
    letter-spacing: 2px;
  }
  .service-line {
    font-size: 28px;
    line-height: 34px;
    font-weight: 700;
    letter-spacing: 1.4px;
    color: var(--burgundy-tagline);
  }
  .service-line.tagline { top: 554px; }
  .service-line.levels { top: 592px; }
</style>
</head>
<body>
  <main class="business-card">
    <svg class="rider-illustration" viewBox="0 0 336 532" role="img"
         aria-label="Broad-lined burgundy outline of a dressage rider in top hat and tailcoat on a collected horse, facing the viewer">
      <defs>
        <linearGradient id="artTone" x1="0" y1="0" x2="0" y2="1">
          <stop offset="0" stop-color="var(--rose-art-light)" stop-opacity="0.45"/>
          <stop offset="0.8" stop-color="var(--rose-art)" stop-opacity="0.55"/>
          <stop offset="1" stop-color="var(--rose-art)" stop-opacity="0"/>
        </linearGradient>
      </defs>
      <rect x="0" y="0" width="336" height="532" rx="18" fill="url(#artTone)"/>
    </svg>

    <svg class="card-frame" viewBox="0 0 1200 693" aria-hidden="true">
      <g fill="none" stroke="var(--burgundy-frame)" stroke-width="7" stroke-linecap="square">
        <path d="M55 44 L900 41"/>
        <path d="M1024 44 L1146 42"/>
        <path d="M55 44 L54 638"/>
        <path d="M54 638 L790 640"/>
        <path d="M1146 42 L1145 632"/>
      </g>
    </svg>

    <h1 class="contact-name">Dale Ferrin</h1>
    <p class="contact-phone">612-374-2059</p>
    <p class="service-line tagline">Classical dressage training for the modern American</p>
    <p class="service-line levels">Clinics, lessons, training level -Prix St. George</p>
  </main>
</body>
</html>
```